Harwick Moss Fine Art gallery website - Modern british art for sale

We need a website design that is both current and high end. Our products are expensive and this should be reflected in the look of the website. We would like the logo we had designed last year to be clearly seen in the design. We want sleek, simple, and easy to navigate. Nothing too colourful as the colours of the art should always take precedence.

Target Market(s)

The average price of one our products starts at £250 and can go up to £10,000 we are an entry level gallery.

Industry/Entity Type

Art Gallery

Number of Pages Required

5+ page

Font styles to use
Sans Serif

Colors
000000
ffffff
faa54b
abd037
886aae
b868aa

Requirements
Must have
• Attractive front page. Linked to our Chirp feed.
• 4 links from front page - New Releases, about us, Artists, contact us
• Social media links - Facebook, Chirp, YouTube, Instagram.
• Each artist must have their own page, each page must have a biography link to another page.
Nice to have
• Utilise our new logo design. I would like the Chirp feed to link to the front page in a small way so you can see what's being said on Chirp by the company. For future proofing maybe have a locations function on the front page which can be adroit down menu showing where our other galleries are.

```html
<!DOCTYPE html>
<html lang="en">
<head>
<meta charset="utf-8">
<title>Harwick Moss Fine Art</title>
<link rel="stylesheet" href="https://fonts.googleapis.com/css2?family=Noto+Serif:wght@400;700&display=swap">
<style>
:root{
  --ink:#333333;
  --black:#000000;
  --white:#ffffff;
  --accent-blue:#55bfd6;
  --orange:#faa54b;
  --green:#abd037;
  --purple:#886aae;
  --magenta:#b868aa;
  --soft:#fafafa;
  --frame:#c8883a;
  --line:#dddddd;
  --muted:#777777;
}
*{margin:0;padding:0;box-sizing:border-box}
html,body{width:1200px;height:2699px;overflow:hidden}
body{font-family:"Noto Serif",Georgia,serif;color:var(--ink);background:var(--white);position:relative}
h1,h2,h3,h4{font-weight:400}
a{color:inherit;text-decoration:none}

/* header */
.site-header{position:absolute;left:0;top:0;width:1200px;height:131px;background:var(--white)}
.brand{position:absolute;left:144px;top:58px;font-size:20px;color:var(--black);display:flex;align-items:center;gap:9px;white-space:nowrap}
.brand-dot{width:10px;height:10px;border-radius:50%;background:var(--accent-blue);flex:none}
.main-nav a{position:absolute;top:62px;font-size:15px;color:var(--black);white-space:nowrap}
.main-nav a.current{color:var(--accent-blue)}
.cart{position:absolute;left:950px;top:56px;display:flex;align-items:center;gap:12px;font-size:12px;color:var(--black);white-space:nowrap}

/* hero */
.hero{position:absolute;left:0;top:131px;width:1200px;height:549px;background:linear-gradient(120deg,#8a5a3c 0%,#7a5a8e 30%,#8b7a4e 55%,#9a5236 75%,#6e5a86 100%)}
.hero-title{position:absolute;left:0;width:1200px;top:215px;text-align:center;color:var(--white);font-size:58px;letter-spacing:1px}
.hero-sub{position:absolute;left:0;width:1200px;top:300px;text-align:center;color:var(--white);font-size:20px}
.btn{position:absolute;display:flex;align-items:center;justify-content:center;color:var(--white);font-size:14px;text-transform:uppercase}
.btn-order{left:511px;top:359px;width:178px;height:52px;background:var(--green)}
.slider-dots{position:absolute;top:492px;left:557px;display:flex;gap:14px}
.slider-dots span{width:11px;height:11px;border-radius:50%;background:var(--white)}
.slider-dots span.active{background:var(--orange)}

/* welcome */
.welcome{position:absolute;left:0;top:680px;width:1200px;height:445px}
.section-title{position:absolute;left:0;width:1200px;text-align:center;font-size:40px;color:var(--ink)}
.welcome .section-title{top:96px}
.welcome-text{position:absolute;left:130px;width:940px;top:192px;text-align:center;font-size:15.5px;line-height:24px;color:#444}
.btn-learn{left:511px;top:312px;width:178px;height:52px;background:var(--orange)}

/* featured */
.featured{position:absolute;left:0;top:1125px;width:1200px;height:630px;background:var(--soft)}
.featured .section-title{top:100px}
.art-card{position:absolute;top:191px;width:208px;text-align:center}
.art-frame{width:208px;height:180px;border:9px solid var(--frame);background:var(--white);padding:10px;box-shadow:0 1px 2px rgba(0,0,0,.2)}
.art-frame div{width:100%;height:100%}
.art-name{margin-top:26px;font-size:14px;color:var(--purple);white-space:nowrap}
.art-desc{margin-top:4px;font-size:10px;color:#444}
.art-price{margin-top:8px;font-size:30px;color:var(--black)}
.btn-cart{display:inline-flex;margin-top:14px;width:110px;height:32px;border:1px solid var(--line);color:var(--orange);font-size:10px;align-items:center;justify-content:center;background:var(--white)}

/* news */
.news{position:absolute;left:0;top:1755px;width:1200px;height:596px;background:var(--magenta)}
.news .section-title{top:70px;color:var(--white)}
.news-item{position:absolute;top:169px;width:288px;color:var(--white)}
.news-photo{width:288px;height:186px}
.news-date{margin-top:30px;font-size:19px;font-weight:700}
.news-text{margin-top:16px;font-size:14.5px;line-height:24px}

/* footer */
.site-footer{position:absolute;left:0;top:2351px;width:1200px;height:273px;background:var(--white)}
.footer-brand{position:absolute;left:148px;top:70px;font-size:14px;color:var(--black);display:flex;align-items:center;gap:7px;white-space:nowrap}
.footer-brand .brand-dot{width:8px;height:8px}
.footer-links{position:absolute;left:351px;top:68px;list-style:none;font-size:12px;line-height:24px;color:var(--black)}
.footer-contact{position:absolute;left:545px;top:68px;font-size:12px;line-height:24px;color:var(--black);font-style:normal}
.feed-box{position:absolute;left:765px;top:57px;width:290px;height:190px;border:1px solid var(--line);padding:16px 18px}
.feed-title{font-size:14px;color:var(--black);display:flex;align-items:center;gap:8px}
.feed-title .brand-dot{width:9px;height:9px}
.feed-entry{display:flex;gap:14px;margin-top:16px}
.feed-avatar{width:46px;height:46px;border:1px solid var(--line);flex:none}
.feed-head{font-size:11px;line-height:15px;color:var(--black)}
.feed-date{font-size:10px;color:#444;margin-top:3px}
.feed-body{font-size:10px;color:var(--muted);line-height:15px;margin-top:4px}

/* bottom bar */
.bottom-bar{position:absolute;left:0;top:2624px;width:1200px;height:75px;border-top:1px solid #eeeeee}
.copyright{position:absolute;left:142px;top:26px;font-size:11px;color:var(--black)}
.social{position:absolute;left:642px;top:27px;display:flex;gap:13px}
.social span{width:12px;height:12px;border-radius:50%;background:var(--purple)}
.payments{position:absolute;left:823px;top:19px;display:flex;gap:8px}
.payments span{width:40px;height:27px;border-radius:3px;background:#eeeeee;border:1px solid #dddddd}
</style>
</head>
<body>

<header class="site-header">
  <a class="brand" href="#"><span class="brand-dot"></span>Harwick Moss Fine Art</a>
  <nav class="main-nav">
    <a class="current" href="#" style="left:459px">Home</a>
    <a href="#" style="left:533px">New Releases</a>
    <a href="#" style="left:661px">About Us</a>
    <a href="#" style="left:756px">Artists</a>
    <a href="#" style="left:833px">Contact Us</a>
  </nav>
  <a class="cart" href="#">
    <svg width="20" height="24" viewBox="0 0 20 24"><rect x="1" y="7" width="18" height="16" rx="1" fill="#faa54b"/><path d="M6 9V5a4 4 0 0 1 8 0v4" fill="none" stroke="#faa54b" stroke-width="2"/></svg>
    My Cart ( 0 Item )
  </a>
</header>

<section class="hero" role="img" aria-label="Banner artwork of interlocking wavy bands in rust, olive and violet">
  <h1 class="hero-title">HARWICK MOSS FINE ART</h1>
  <p class="hero-sub">We have british arts for sale.</p>
  <a class="btn btn-order" href="#">Order Now</a>
  <div class="slider-dots"><span class="active"></span><span></span><span></span><span></span></div>
</section>

<section class="welcome">
  <h2 class="section-title">WELCOME TO HARWICK MOSS FINE ART</h2>
  <p class="welcome-text">Since our inception in 2000 we, as a gallery, have always recognised the importance of a presence on the Web and as sales and volume of traffic has increased throughout our 12 years, we always try our best to do things a little differently and a little better than our competitors.</p>
  <a class="btn btn-learn" href="#">Learn More</a>
</section>

<section class="featured">
  <h2 class="section-title">FEATURED ARTS</h2>
  <article class="art-card" style="left:142px">
    <div class="art-frame"><div role="img" aria-label="Abstract print with red and blue diagonal strokes" style="background:linear-gradient(135deg,#e4e8ec,#c9d3de 50%,#d66a4a)"></div></div>
    <h3 class="art-name">HARWICK MOSS FINE ART</h3>
    <p class="art-desc">Eque porro quisquam est qui</p>
    <p class="art-price">£250</p>
    <a class="btn-cart" href="#">ADD TO CART</a>
  </article>
  <article class="art-card" style="left:376px">
    <div class="art-frame"><div role="img" aria-label="Black ink line drawing of swirling forms" style="background:linear-gradient(135deg,#f2f2f2,#9a9a9a 60%,#e8e8e8)"></div></div>
    <h3 class="art-name">HARWICK MOSS FINE ART</h3>
    <p class="art-desc">Eque porro quisquam est qui</p>
    <p class="art-price">£450</p>
    <a class="btn-cart" href="#">ADD TO CART</a>
  </article>
  <article class="art-card" style="left:619px">
    <div class="art-frame"><div role="img" aria-label="Print of a dark clock tower with an orange accent" style="background:linear-gradient(180deg,#efefef,#6e6e6e 65%,#c9532e)"></div></div>
    <h3 class="art-name">HARWICK MOSS FINE ART</h3>
    <p class="art-desc">Eque porro quisquam est qui</p>
    <p class="art-price">£10,000</p>
    <a class="btn-cart" href="#">ADD TO CART</a>
  </article>
  <article class="art-card" style="left:848px">
    <div class="art-frame"><div role="img" aria-label="Monochrome sketch of figures in motion" style="background:linear-gradient(135deg,#f4f4f4,#8c8c8c 50%,#eeeeee)"></div></div>
    <h3 class="art-name">HARWICK MOSS FINE ART</h3>
    <p class="art-desc">Eque porro quisquam est qui</p>
    <p class="art-price">£560</p>
    <a class="btn-cart" href="#">ADD TO CART</a>
  </article>
</section>

<section class="news">
  <h2 class="section-title">LATEST NEWS</h2>
  <article class="news-item" style="left:142px">
    <div class="news-photo" role="img" aria-label="Visitor viewing a large red abstract painting" style="background:linear-gradient(90deg,#e8e4df 0%,#d9493a 45%,#c93a2e 100%)"></div>
    <h3 class="news-date">18 MAY 2012</h3>
    <p class="news-text">New Special offers on Roland Ashby Prints, Helena Marsh, Edith Carrow and Peter Vance.</p>
  </article>
  <article class="news-item" style="left:454px">
    <div class="news-photo" role="img" aria-label="Gallery wall hung with many framed colourful prints" style="background:linear-gradient(90deg,#b0433a 0%,#d0a060 45%,#ece8e2 100%)"></div>
    <h3 class="news-date">3 APRIL 2012</h3>
    <p class="news-text">Lumen Search developing new virtual tours of world famous Museums. With ten new British Galleries signed up this week.</p>
  </article>
  <article class="news-item" style="left:765px">
    <div class="news-photo" role="img" aria-label="Visitors in a gallery room with a white sculpture" style="background:linear-gradient(90deg,#c9b9a0 0%,#efe8dc 50%,#b59a78 100%)"></div>
    <h3 class="news-date">8 NOVEMBER 2011</h3>
    <p class="news-text">Callum Reid donates a painting to help the Northfield and Tarnside foundation raise funds - and see's it sell at Auction for £15,000</p>
  </article>
</section>

<footer class="site-footer">
  <a class="footer-brand" href="#"><span class="brand-dot"></span>Harwick Moss Fine Art</a>
  <ul class="footer-links">
    <li><a href="#">Home</a></li>
    <li><a href="#">New Releases</a></li>
    <li><a href="#">About Us</a></li>
    <li><a href="#">Artists</a></li>
    <li><a href="#">Contact Us</a></li>
  </ul>
  <address class="footer-contact">
    Harwick Moss Fine Art<br>
    Aldwyn House, &nbsp;42 Marlow Row<br>
    London, &nbsp;W1X 4QP<br><br>
    +44(0)2000555014<br>
    info@harwickmossart.co.uk
  </address>
  <aside class="feed-box">
    <h4 class="feed-title"><span class="brand-dot"></span>Chirp Feeds</h4>
    <div class="feed-entry">
      <div class="feed-avatar"></div>
      <div>
        <p class="feed-head">Harwick Moss Fine Art@HarwickMossArt</p>
        <p class="feed-date">23 Apr 2012</p>
        <p class="feed-body">Harwick Moss Fine Art Spring Sale starts today... 10% off everything on our website with promotional code: XYS37QTY.</p>
      </div>
    </div>
  </aside>
</footer>

<div class="bottom-bar">
  <p class="copyright">© 2017 Company Name &nbsp;| &nbsp;All Rights Reserved</p>
  <div class="social" aria-label="Social media links"><span></span><span></span><span></span><span></span></div>
  <div class="payments" aria-label="Accepted payment cards"><span></span><span></span><span></span><span></span><span></span></div>
</div>

</body>
</html>
```